Corporate Business Card

Very professional, Modern, Not to busy, include phone address email, website
(253) 617-4930, 18761 52nd Avenue S, Kent, WA 98047, martin@plumlinegroup.com, varkoworks.com

Target Market(s)

Manufacturing

Industry/Entity Type

Aero, machining, manufacturing, Off road racing

Contact Information for Business Card

Phone, address email, website

```html
<!DOCTYPE html>
<html lang="en">
<head>
<meta charset="utf-8">
<title>Varko Industries – Business Card</title>
<link href="https://fonts.googleapis.com/css2?family=Montserrat:wght@500;700&display=swap" rel="stylesheet">
<style>
  :root {
    --navy: #17377a;
    --navy-deep: #132f68;
    --red: #d8222b;
    --silver: #c9cacd;
    --ink: #1b1b1b;
    --paper: #ffffff;
    --backdrop: #2a2a2c;
  }
  * { margin: 0; padding: 0; box-sizing: border-box; }
  html, body { width: 1200px; height: 1015px; overflow: hidden; }
  body {
    background: var(--backdrop);
    font-family: "Montserrat", sans-serif;
    position: relative;
  }
  .card {
    position: absolute;
    width: 580px;
    height: 331px;
    overflow: hidden;
    box-shadow: 0 14px 30px rgba(0,0,0,.45);
  }
  .card-front { left: 70px; top: 130px; background: var(--navy); }
  .card-back { left: 550px; top: 530px; background: var(--paper); }

  .brand {
    position: absolute;
    font-weight: 700;
    white-space: nowrap;
    letter-spacing: .5px;
  }
  .card-front .brand {
    color: var(--silver);
    font-size: 50px;
    left: 70px; top: 112px;
  }
  .card-front .brand-rule {
    position: absolute;
    left: 72px; top: 190px;
    width: 200px; height: 2px;
    background: var(--silver);
  }
  .card-back .brand {
    color: var(--navy);
    font-size: 24px;
    left: 232px; top: 44px;
  }
  .card-back .brand-rule {
    position: absolute;
    left: 234px; top: 84px;
    width: 120px; height: 2px;
    background: var(--navy);
  }

  .back-sweep { position: absolute; inset: 0; }

  .address {
    position: absolute;
    left: 44px; top: 110px;
    font-size: 13px;
    font-weight: 500;
    line-height: 1.4;
    color: var(--ink);
  }
  .contact-list {
    position: absolute;
    left: 44px; top: 168px;
    list-style: none;
    font-size: 13px;
    font-weight: 500;
    color: var(--ink);
  }
  .contact-list li {
    display: flex;
    align-items: center;
    gap: 9px;
    height: 22px;
  }
  .contact-list svg { width: 12px; height: 12px; fill: var(--red); flex: none; }
</style>
</head>
<body>

<section class="card card-front" aria-label="Card front">
  <div class="brand">Varko Industries</div>
  <div class="brand-rule"></div>
</section>

<section class="card card-back" aria-label="Card back">
  <svg class="back-sweep" viewBox="0 0 580 331" preserveAspectRatio="none" aria-hidden="true">
    <path d="M0,305 C310,292 490,220 560,0 L580,0 L580,331 L0,331 Z" fill="var(--navy-deep)"/>
    <path d="M0,287 C300,276 472,204 545,22 C488,212 312,286 0,297 Z" fill="var(--red)"/>
  </svg>

  <div class="brand">Varko Industries</div>
  <div class="brand-rule"></div>

  <p class="address">18761 52nd Avenue S<br>Kent, WA 98047</p>

  <ul class="contact-list">
    <li>
      <svg viewBox="0 0 24 24"><path d="M6.6 10.8a15.1 15.1 0 0 0 6.6 6.6l2.2-2.2a1 1 0 0 1 1-.25 11.4 11.4 0 0 0 3.6.57 1 1 0 0 1 1 1V20a1 1 0 0 1-1 1A17 17 0 0 1 3 4a1 1 0 0 1 1-1h3.5a1 1 0 0 1 1 1c0 1.25.2 2.45.57 3.57a1 1 0 0 1-.25 1z"/></svg>
      (253) 617-4930
    </li>
    <li>
      <svg viewBox="0 0 24 24"><path d="M2 5h20v14H2z"/><path d="M3.5 6.5 12 13l8.5-6.5" fill="none" stroke="#fff" stroke-width="1.6"/></svg>
      martin@plumlinegroup.com
    </li>
    <li>
      <svg viewBox="0 0 24 24"><circle cx="12" cy="12" r="10"/><path d="M2 12h20M12 2c3 3 3 17 0 20M12 2c-3 3-3 17 0 20" fill="none" stroke="#fff" stroke-width="1.4"/></svg>
      www.varkoworks.com
    </li>
  </ul>
</section>

</body>
</html>
```